Website for IT consulting Company

I need a website upgrade, the existing site content is ok, I would also like to add a testimonial page, the site should be something that is easy for us to update content. You use the content from www.kelvanbrook.com as an example. I will also post update logo and artwork. I also need a contact form with some type of validation or captcha.

I added Coded to the Project

Please omit Address maps

Target Market(s)

small business, service oriented companies. We provide IT Consulting, support and mangement

Industry/Entity Type

Information Technology

Coding

Number of Pages Required

1 page

Font styles to use
Serif
Sans Serif

Requirements
Must have
• Contain logo attached, and content from existing web site www.kelvanbrook.com.
• Also need to update content easily, and be movable to different platforms.
• There is a catch phrase
• "Let us worry about your technology…” “ so you don’t have to!”
• Should be included.
Nice to have
• Testimonial page, Project page where we can post new and past projects and pictures
Should not have
• none

```html
<!DOCTYPE html>
<html lang="en">
<head>
<meta charset="UTF-8">
<title>Kelvanbrook Group – IT Solutions</title>
<link rel="stylesheet" href="https://fonts.googleapis.com/css2?family=Nunito:wght@400;600;700&family=Open+Sans:wght@400;600&family=Oswald:wght@400;500&display=swap">
<style>
:root{
  --blue:#3d8fd6;
  --blue-deep:#2a6fb5;
  --band:#4a95da;
  --ink:#222;
  --muted:#777;
  --light:#f4f4f4;
  --footer:#1c1d20;
  --footer-base:#0b0b0c;
  --white:#fff;
}
*{margin:0;padding:0;box-sizing:border-box}
html,body{width:1200px;height:2740px;overflow:hidden}
body{font-family:"Nunito",Arial,sans-serif;color:var(--ink);background:var(--white);position:relative}
.section{position:absolute;left:0;width:1200px}

/* header */
.site-header{top:0;height:110px;background:var(--white)}
.brand{position:absolute;left:88px;top:40px;display:flex;align-items:center;gap:10px}
.brand-mark{width:30px;height:30px;background:var(--blue)}
.brand-name{font-size:27px;font-weight:700;color:var(--blue);letter-spacing:.5px;line-height:1}
.main-nav{position:absolute;left:497px;top:42px;display:flex;gap:4px}
.main-nav a{font-size:16px;color:var(--ink);text-decoration:none;padding:6px 18px;border:2px solid transparent;border-radius:20px;letter-spacing:.3px;white-space:nowrap}
.main-nav a.active{color:var(--blue);border-color:var(--blue)}

/* hero */
.hero{top:110px;height:544px;background:linear-gradient(100deg,#050608 0%,#0b0f16 45%,#15304f 70%,#0a1a2e 100%)}
.hero-visual{position:absolute;right:0;top:0;width:620px;height:544px;background:radial-gradient(circle at 55% 45%,rgba(90,170,240,.55),rgba(30,80,140,.25) 45%,transparent 70%)}
.hero-title{position:absolute;left:88px;top:234px;font-family:"Oswald",Arial,sans-serif;font-size:46px;font-weight:500;color:var(--white);letter-spacing:.5px;white-space:nowrap}
.hero-sub{position:absolute;left:88px;top:294px;font-family:"Open Sans",Arial,sans-serif;font-size:28px;color:var(--white);white-space:nowrap}
.hero-arrows{position:absolute;left:88px;top:356px;display:flex;gap:6px}
.hero-arrows span{width:28px;height:28px;border-radius:50%;background:#2a2a2a;display:flex;align-items:center;justify-content:center}

/* call band */
.cta-band{top:654px;height:98px;background:var(--band)}
.cta-text{position:absolute;left:163px;top:33px;font-size:27px;color:var(--white);letter-spacing:.5px;white-space:nowrap}
.cta-button{position:absolute;left:828px;top:24px;width:210px;height:50px;border-radius:25px;background:var(--white);color:var(--ink);font-size:20px;display:flex;align-items:center;justify-content:center}

/* headings */
.heading{position:absolute;left:0;width:1200px;text-align:center;font-size:30px;font-weight:400;letter-spacing:.5px}
.subheading{position:absolute;left:0;width:1200px;text-align:center;font-size:17px;color:var(--muted)}

/* services */
.services{top:752px;height:530px}
.service{position:absolute;width:300px;text-align:center}
.service-icon{width:113px;height:113px;margin:0 auto;border-radius:50%;border:6px solid #f0f0f0;box-shadow:0 0 0 1px #e2e2e2;display:flex;align-items:center;justify-content:center}
.service-title{height:46px;margin-top:20px;font-size:16px;line-height:21px;display:flex;align-items:flex-end;justify-content:center;letter-spacing:.3px}
.service-text{margin-top:14px;font-size:11.5px;line-height:17px;color:var(--muted);padding:0 14px}
.read-more{margin-top:12px;font-size:13px;color:var(--blue)}

/* about split */
.about{top:1282px;height:367px}
.about-photo{position:absolute;left:0;top:0;width:577px;height:367px;background:linear-gradient(120deg,#c7d8e6,#7f9bb4 55%,#3e5d7e)}
.about-panel{position:absolute;left:577px;top:0;width:623px;height:367px;background:linear-gradient(135deg,#2f7cc4,#1e5ea0)}
.about-kicker{position:absolute;left:48px;top:54px;font-size:22px;color:var(--white);font-weight:400}
.about-title{position:absolute;left:48px;top:80px;font-size:29px;font-weight:400;color:var(--white);letter-spacing:.5px}
.about-text{position:absolute;left:48px;top:128px;width:484px;font-family:"Open Sans",Arial,sans-serif;font-size:14.5px;line-height:24.5px;color:var(--white);text-align:justify}
.about-button{position:absolute;left:48px;top:290px;width:104px;height:30px;border-radius:15px;background:var(--white);color:var(--ink);font-size:12px;display:flex;align-items:center;justify-content:center}

/* support cards */
.support{top:1649px;height:475px}
.cards{position:absolute;left:88px;top:204px;display:flex;gap:16px}
.card{width:243px;height:192px;background:var(--white);box-shadow:0 1px 4px rgba(0,0,0,.2)}
.card-photo{height:141px}
.card-label{height:51px;display:flex;align-items:center;justify-content:center;font-size:13.5px;letter-spacing:.3px}
.slider-arrow{position:absolute;top:272px}

/* testimonials */
.testimonials{top:2124px;height:314px;background:var(--light)}
.quote{position:absolute;top:148px;width:460px;height:100px}
.avatar{position:absolute;left:0;top:-8px;width:92px;height:92px;border-radius:50%;background:#c9b8a6;border:3px solid var(--white);box-shadow:0 0 0 1px #ddd}
.quote-text{position:absolute;left:116px;top:0;width:336px;font-size:11.5px;line-height:22px;color:#555;text-align:justify}
.quote-text .mark{color:var(--blue);font-size:20px;line-height:0}
.quote-role{position:absolute;left:116px;top:82px;font-size:11.5px;font-weight:700;color:#333}

/* footer */
.site-footer{top:2438px;height:219px;background:var(--footer)}
.footer-brand{position:absolute;left:88px;top:100px;display:flex;align-items:center;gap:10px}
.footer-brand .brand-mark{width:24px;height:24px}
.footer-brand .brand-name{font-size:22px;color:var(--blue)}
.footer-col{position:absolute;top:52px;color:var(--white)}
.footer-col h4{font-size:14px;font-weight:400;letter-spacing:.5px;margin-bottom:20px}
.footer-col p{font-size:11.5px;line-height:22px}
.newsletter{display:flex;margin-top:14px}
.newsletter .field{width:148px;height:32px;background:var(--white);font-size:11px;color:#999;padding:0 8px;display:flex;align-items:center}
.newsletter .submit{width:56px;height:32px;background:var(--blue);color:var(--white);font-size:11px;display:flex;align-items:center;justify-content:center}
.social{display:flex;gap:12px;margin-top:4px}
.social span{width:26px;height:26px;border-radius:4px;background:var(--white)}

.copyright{top:2657px;height:83px;background:var(--footer-base);color:var(--white);font-size:13px;display:flex;align-items:center;justify-content:center}
</style>
</head>
<body>

<header class="section site-header">
  <div class="brand"><span class="brand-mark"></span><span class="brand-name">KELVANBROOK</span></div>
  <nav class="main-nav">
    <a class="active" href="#">HOME</a>
    <a href="#">ABOUT</a>
    <a href="#">CONTACT</a>
    <a href="#">SUPPORT</a>
    <a href="#">CLIENTS</a>
    <a href="#">CAREERS</a>
  </nav>
</header>

<section class="section hero">
  <div class="hero-visual" role="img" aria-label="Hand holding a glowing laptop surrounded by network icons"></div>
  <h1 class="hero-title">KELVANBROOK GROUP</h1>
  <p class="hero-sub">Neque porro quisquam est qui</p>
  <div class="hero-arrows">
    <span><svg width="10" height="12" viewBox="0 0 10 12"><path d="M7 1 2 6l5 5" stroke="#fff" stroke-width="2" fill="none"/></svg></span>
    <span><svg width="10" height="12" viewBox="0 0 10 12"><path d="M3 1l5 5-5 5" stroke="#fff" stroke-width="2" fill="none"/></svg></span>
  </div>
</section>

<section class="section cta-band">
  <p class="cta-text">IT SOLUTIONS THAT WORK FOR YOUR BUSINESS.</p>
  <a class="cta-button">LEARN MORE »</a>
</section>

<section class="section services">
  <h2 class="heading" style="top:80px">OUR SERVICES</h2>
  <p class="subheading" style="top:122px">porro quisquam est qui dolorem</p>

  <div class="service" style="left:100px;top:185px">
    <div class="service-icon">
      <svg width="40" height="36" viewBox="0 0 40 36" fill="#2d8ad6"><circle cx="14" cy="20" r="10"/><circle cx="14" cy="20" r="4" fill="#fff"/><circle cx="30" cy="10" r="7"/><circle cx="30" cy="10" r="3" fill="#fff"/></svg>
    </div>
    <div class="service-title">MANAGED IT SOLUTIONS</div>
    <p class="service-text">Our staff will design, service, administer and maintain your IT needs. We are well versed on all major operating system, and network appliances</p>
    <p class="read-more">READ MORE »</p>
  </div>

  <div class="service" style="left:456px;top:185px">
    <div class="service-icon">
      <svg width="40" height="36" viewBox="0 0 40 36"><rect x="2" y="3" width="36" height="24" rx="2" fill="#2d8ad6"/><rect x="16" y="27" width="8" height="5" fill="#2d8ad6"/><rect x="11" y="32" width="18" height="2" fill="#2d8ad6"/></svg>
    </div>
    <div class="service-title">REMOTE DIAGNOSTIC<br>AND SUPPORT</div>
    <p class="service-text">Do you need a quick solution to a technical problem? With our live remote-assistance tool, a member of our support team can view</p>
    <p class="read-more">READ MORE »</p>
  </div>

  <div class="service" style="left:803px;top:185px">
    <div class="service-icon">
      <svg width="36" height="36" viewBox="0 0 36 36" fill="#2d8ad6"><rect x="6" y="3" width="16" height="22" rx="1"/><rect x="14" y="11" width="16" height="22" rx="1" stroke="#fff" stroke-width="2"/></svg>
    </div>
    <div class="service-title">IT INFRASTRUCTURE DESIGN<br>AND INSTALLATION</div>
    <p class="service-text">Do you have more than one site? Do you need remote access? We can design and implement LANS/WANS and VPN's. Make your important</p>
    <p class="read-more">READ MORE »</p>
  </div>
</section>

<section class="section about">
  <div class="about-photo" role="img" aria-label="Three colleagues working together at a laptop in a bright office"></div>
  <div class="about-panel">
    <p class="about-kicker">Flexible solutions for</p>
    <h2 class="about-title">YOUR BUSINESS NEEDS</h2>
    <p class="about-text">Kelvanbrook is a technology solution provider based in Houston, Texas. Our goal is to make technology a non-issue for individuals and small to medium size businesses ranging from 5 to 150 Users. Kelvanbrook has the experience, the tools, high-level technology solutions and training to power your business and your work force. We understand that all business's have one goal in common!</p>
    <a class="about-button">Read More »</a>
  </div>
</section>

<section class="section support">
  <h2 class="heading" style="top:98px">IT SUPPORT SOLUTIONS</h2>
  <p class="subheading" style="top:138px">Neque porro quisquam est qui dolorem</p>
  <svg class="slider-arrow" style="left:50px" width="20" height="40" viewBox="0 0 20 40"><path d="M17 2 3 20l14 18" stroke="#bbb" stroke-width="2" fill="none"/></svg>
  <div class="cards">
    <div class="card"><div class="card-photo" role="img" aria-label="Support agent with headset at a computer" style="background:linear-gradient(135deg,#eef2f5,#b9c6d1)"></div><div class="card-label">NETWORK ADMINISTRATION</div></div>
    <div class="card"><div class="card-photo" role="img" aria-label="Technician working at a desktop computer" style="background:linear-gradient(135deg,#d9d7d2,#8f8a84)"></div><div class="card-label">DESKTOP SUPPORT</div></div>
    <div class="card"><div class="card-photo" role="img" aria-label="Engineers in a server room working on cabling" style="background:linear-gradient(135deg,#9aa6b2,#3e4a57)"></div><div class="card-label">NETWORK CABLING</div></div>
    <div class="card"><div class="card-photo" role="img" aria-label="Hand touching a glowing wireless network interface" style="background:linear-gradient(135deg,#2e5a82,#0f1f33)"></div><div class="card-label">WIRELESS NETWORKS</div></div>
  </div>
  <svg class="slider-arrow" style="left:1124px" width="20" height="40" viewBox="0 0 20 40"><path d="M3 2l14 18L3 38" stroke="#bbb" stroke-width="2" fill="none"/></svg>
</section>

<section class="section testimonials">
  <h2 class="heading" style="top:52px">TESTIMONIALS</h2>
  <div class="quote" style="left:98px">
    <div class="avatar" role="img" aria-label="Portrait of a client"></div>
    <p class="quote-text"><span class="mark">“</span> It is a long established fact that a reader will be distracted by the readable content of a page when looking at its layout. The point of using Lorem Ipsum <span class="mark">”</span></p>
    <p class="quote-role">CEO, INSURANCE BROKERAGE</p>
  </div>
  <div class="quote" style="left:654px">
    <div class="avatar" role="img" aria-label="Portrait of a client"></div>
    <p class="quote-text"><span class="mark">“</span> It is a long established fact that a reader will be distracted by the readable content of a page when looking at its layout. The point of using Lorem Ipsum <span class="mark">”</span></p>
    <p class="quote-role">CEO, INFORMATION TECHNOLOGY CONSULTANCY</p>
  </div>
</section>

<footer class="section site-footer">
  <div class="footer-brand"><span class="brand-mark"></span><span class="brand-name">KELVANBROOK</span></div>
  <div class="footer-col" style="left:356px">
    <h4>CONTACT US</h4>
    <p>Address : 12 Ferrow Lane, Eastgate<br>Bristol, BS4 2QL<br>Phone : 555-014-2290.<br>Email : info@kelvanbrook.com</p>
  </div>
  <div class="footer-col" style="left:655px">
    <h4>SIGN UP FOR NEWSLETTER</h4>
    <p style="line-height:17px;width:190px">Your about us information would fit here nicely.</p>
    <div class="newsletter"><span class="field">Email address</span><span class="submit">Submit</span></div>
  </div>
  <div class="footer-col" style="left:947px">
    <h4>FOLLOW US OUT THERE</h4>
    <div class="social"><span></span><span></span><span></span><span></span></div>
  </div>
</footer>

<div class="section copyright">Copyright © 2017. All Rights Reserved</div>

</body>
</html>
```